Wine Bottle Label Logo Design

My fiancé and I are getting married in September and we made homemade wine which will be given to the guests as a wedding favor. We need label/logo for our wine bottles. We were looking for something rustic yet modern and simple. We had an idea for beige and cranberry colored wine stained, weathered, imperfect heart. Things that will need to be incorporated into the label design are as follows:
Our last name and also the name of the wine: Carudi
The year: 2012
Where is says Alcohol Content on a wine bottle normally write: Alcohol: Deceiving% by vol.
Type of wine: Red Wine
Incorporate our wedding date: Foot Stomped and Bottled for Marla and Ned's Wedding Day 9/28/13

```html
<!DOCTYPE html>
<html lang="en">
<head>
<meta charset="utf-8">
<title>Carudi Wine Labels</title>
<link rel="stylesheet" href="https://fonts.googleapis.com/css2?family=Nothing+You+Could+Do&display=swap">
<style>
  :root {
    --paper: #ffffff;
    --label: #ffffff;
    --stain-dark: #6f4f4b;
    --stain-light: #a3837b;
    --ribbon: #a78c76;
    --ink: #4d3f3d;
    --ink-soft: #6a5b58;
    --on-stain: #f6eeea;
  }
  * { margin: 0; padding: 0; box-sizing: border-box; }
  html, body {
    width: 1085px;
    height: 1200px;
    overflow: hidden;
    background: var(--paper);
  }
  .canvas {
    position: relative;
    width: 1085px;
    height: 1200px;
    font-family: "Nothing You Could Do", cursive;
    color: var(--ink);
  }
  .label {
    position: absolute;
    width: 224px;
    height: 224px;
    border-radius: 50%;
    background: var(--label);
    box-shadow: 0 0 0 1px #ece6e3;
    overflow: hidden;
  }
  .label--front { left: 204px; top: 630px; }
  .label--back  { left: 666px; top: 635px; }

  .stain-mark {
    position: absolute;
    border-radius: 46% 46% 50% 50% / 40% 40% 60% 60%;
    background: radial-gradient(circle at 40% 35%, var(--stain-light), var(--stain-dark));
    opacity: 0.9;
  }
  .label--front .stain-mark { left: 41px; top: 25px; width: 148px; height: 135px; }
  .label--back .stain-mark  { left: 90px; top: 6px; width: 44px; height: 44px; }

  .wine-name {
    position: absolute;
    left: 0;
    width: 100%;
    text-align: center;
    color: var(--on-stain);
    line-height: 1;
  }
  .label--front .wine-name { top: 66px; font-size: 34px; }
  .label--back .wine-name  { top: 21px; font-size: 11px; }

  .dedication-band {
    position: absolute;
    left: 41px;
    top: 166px;
    width: 150px;
    height: 24px;
    background: var(--ribbon);
    clip-path: polygon(0 0, 100% 0, 94% 50%, 100% 100%, 0 100%, 6% 50%);
    color: var(--on-stain);
    font-size: 6px;
    line-height: 8px;
    text-align: center;
    padding: 4px 12px 0;
  }

  .vintage {
    position: absolute;
    top: 70px;
    width: 100%;
    text-align: center;
    font-size: 14px;
  }
  .wine-type {
    position: absolute;
    top: 90px;
    width: 100%;
    text-align: center;
    font-size: 8px;
    color: var(--ink-soft);
  }
  .tasting-note {
    position: absolute;
    left: 27px;
    top: 103px;
    width: 170px;
    text-align: center;
    font-size: 10px;
    line-height: 20px;
    letter-spacing: 0.4px;
  }
  .alcohol {
    position: absolute;
    top: 204px;
    width: 100%;
    text-align: center;
    font-size: 8px;
    color: var(--ink-soft);
  }
</style>
</head>
<body>
<main class="canvas">
  <section class="label label--front">
    <div class="stain-mark" role="img" aria-label="Weathered wine-stained heart in cranberry and beige"></div>
    <p class="wine-name">Carudi</p>
    <p class="dedication-band">Foot Stomped and Bottled for Marla and Ned's Wedding Day 9/28/13</p>
  </section>

  <section class="label label--back">
    <div class="stain-mark" role="img" aria-label="Small wine-stained heart"></div>
    <p class="wine-name">Carudi</p>
    <p class="vintage">2012</p>
    <p class="wine-type">Red Wine</p>
    <p class="tasting-note">Aged outdoors during the cold winter months to allow for a slower fermentation process. Its like a warm sweet hug in a bottle.</p>
    <p class="alcohol">Alcohol: Deceiving% by vol.</p>
  </section>
</main>
</body>
</html>
```